VC Liquidity Transformation Case Study Design

2-Page VC Case Study Brochure Concept
We are looking for visual design concepts, not finished production files.
This project explores a 2-page institutional brochure for Brisket Partners that:
Page 1 → Explains our differentiated approach to venture-backed technology exits
Page 2 → Demonstrates how we convert long-tenured portfolio companies into strategic outcomes
The attached Design Guide includes:
• Page wireframe
• Referenced visuals
• Icon direction
• Tone and design rules
Designers should use this as a structural guide, not a constraint.

- BP Process Diagram: several modifications needed to the images to be recreated (various images attached)
- Brisket Partners 2-Page Brochure small (B1 and Final F1 - psd files) are my current 2 page brochure. Leverage if you'd like.
- Logo package: this is the package of Brisket Partners logos

Target Market(s)

Institutional capital investors like Venture capitalists and private equity groups

Industry/Entity Type

investment banking

Font styles to use
Sans Serif

Colors
0054AA
0677BA
7BADD7
CADEEF
E8F1F8

Requirements
Must have
• See design guide
Nice to have
• See design guide
Should not have
• See design guide

```html
<!DOCTYPE html>
<html lang="en">
<head>
<meta charset="utf-8">
<title>Brisket Partners – Two-Page Case Study Brochure</title>
<link rel="stylesheet" href="https://fonts.googleapis.com/css2?family=Cinzel:wght@600;700&family=Open+Sans:wght@400;600;700&display=swap">
<style>
:root{
  --navy:#0b2f6b;
  --blue:#0054AA;
  --mid:#0677BA;
  --sky:#7BADD7;
  --pale:#CADEEF;
  --mist:#E8F1F8;
  --ink:#2b3442;
  --ground:#eef1f5;
  --white:#ffffff;
}
*{box-sizing:border-box;margin:0;padding:0}
html,body{width:893px;height:1200px;overflow:hidden}
body{background:var(--ground);font-family:"Open Sans",Arial,sans-serif;color:var(--ink);position:relative}
.spread{position:absolute;top:316px;left:16px;display:flex;gap:21px}
.page{width:420px;height:568px;background:var(--white);position:relative;box-shadow:0 2px 10px rgba(0,40,90,.18);overflow:hidden}
.serif{font-family:"Cinzel",Georgia,serif}

/* page one */
.masthead{height:74px;display:flex;align-items:center;padding:0 22px;gap:8px;border-bottom:1px solid var(--pale)}
.brand-mark{width:18px;height:18px;background:var(--blue)}
.brand-name{font-weight:700;color:var(--blue);font-size:18px;letter-spacing:2px}
.hero{display:flex;padding:14px 22px 8px;gap:14px}
.hero-text{flex:1}
.hero-title{font-size:21px;line-height:1.15;color:var(--blue);font-weight:700;margin-bottom:10px}
.hero-copy{font-size:7.5px;line-height:1.5;color:var(--ink);margin-bottom:6px}
.hero-copy strong{color:var(--blue)}
.hero-visual{width:160px;height:148px;border-radius:6px;background:linear-gradient(160deg,var(--mist),var(--sky) 55%,var(--mid))}
.section-band{margin:6px 0 0;background:var(--blue);color:var(--white);text-align:center;font-size:9px;font-weight:700;padding:5px 0}
.band-note{font-size:6.5px;text-align:center;color:var(--ink);padding:5px 22px}
.stages{display:flex;gap:4px;padding:4px 22px 10px}
.stage{flex:1;background:var(--mist);border-top:3px solid var(--mid);padding:6px 4px;text-align:center}
.stage b{display:block;font-size:10px;color:var(--blue)}
.stage span{font-size:6px;line-height:1.3;display:block}
.lower{display:flex;gap:12px;padding:4px 22px}
.insight{flex:1}
.insight h3,.snapshot h3{font-size:9.5px;color:var(--blue);margin-bottom:4px}
.insight p{font-size:6.5px;line-height:1.5;margin-bottom:4px}
.snapshot{width:150px;border:1px solid var(--pale);background:var(--mist);padding:8px}
.snapshot ul{list-style:none;font-size:6.5px;line-height:1.6}
.snapshot li::before{content:"▸ ";color:var(--mid)}
.page-foot{position:absolute;bottom:0;left:0;right:0;height:26px;background:var(--navy);color:var(--pale);font-size:6px;display:flex;align-items:center;justify-content:center}

/* page two */
.spread-title{padding:22px 22px 4px;text-align:center;font-size:18px;color:var(--blue);font-weight:700;line-height:1.2}
.spread-sub{text-align:center;font-size:8px;color:var(--mid);margin-bottom:8px}
.diagram{display:block;margin:0 auto}
.lifecycle-title{text-align:center;font-size:17px;color:var(--blue);font-weight:700;margin-top:6px}
.lifecycle-sub{text-align:center;font-size:7px;color:var(--mid);margin-bottom:4px}
.lifecycle-note{font-size:6px;text-align:center;padding:4px 22px;color:var(--ink)}
</style>
</head>
<body>
<main class="spread">

  <!-- Page one -->
  <section class="page page-approach">
    <header class="masthead">
      <span class="brand-mark"></span>
      <span class="brand-name">BRISKET PARTNERS</span>
    </header>

    <div class="hero">
      <div class="hero-text">
        <h1 class="hero-title serif">The Overlooked Majority in Venture Portfolios</h1>
        <p class="hero-copy"><strong>Most venture portfolios contain a considerable set of companies with a stable product, real revenue and no clear path to an exit.</strong></p>
        <p class="hero-copy">These companies tie up capital, time and attention while fund life runs down. We help managers turn them into strategic outcomes.</p>
      </div>
      <div class="hero-visual" role="img" aria-label="Photograph of modern glass architecture in blue tones"></div>
    </div>

    <div class="section-band">The Venture Exit Backlog</div>
    <p class="band-note">Extended holding periods, quiet valuation marks and limited IPO windows leave many companies waiting on exits.</p>
    <div class="stages">
      <div class="stage"><b>8–12</b><span>Years average holding period</span></div>
      <div class="stage"><b>60%</b><span>Of companies lack clear exit</span></div>
      <div class="stage"><b>3x</b><span>Longer than fund plan</span></div>
      <div class="stage"><b>Low</b><span>IPO and M&amp;A volume</span></div>
      <div class="stage"><b>Idle</b><span>Capital waiting on return</span></div>
    </div>

    <div class="lower">
      <div class="insight">
        <h3>Supporting Insight</h3>
        <p>Longer fund periods, quiet valuation marks and crowded exit routes have created a growing population of long-tenured companies.</p>
        <p>Strategic buyers value their technology, teams and customers when the story is told with clear intent.</p>
      </div>
      <aside class="snapshot">
        <h3>Portfolio Reality Snapshot</h3>
        <ul>
          <li>Typical VC portfolio</li>
          <li>Few companies drive returns</li>
          <li>Many hold steady value</li>
          <li>Long tail remains unlisted</li>
        </ul>
      </aside>
    </div>

    <footer class="page-foot">Brisket Partners · Venture Exit Advisory</footer>
  </section>

  <!-- Page two -->
  <section class="page page-outcome">
    <h2 class="spread-title serif">From Long-Tenured Holding<br>to Strategic Outcome</h2>
    <p class="spread-sub">How Brisket Partners enables venture capital recycling.</p>

    <svg class="diagram" width="380" height="250" viewBox="0 0 380 250" font-family="Open Sans, Arial, sans-serif">
      <!-- core box -->
      <rect x="114" y="4" width="152" height="46" fill="#0054AA"/>
      <text x="190" y="19" fill="#E8F1F8" font-size="6" text-anchor="middle">ALIGNED BUYER VERTICALS</text>
      <text x="190" y="37" fill="#fff" font-size="10" font-family="Cinzel, Georgia, serif" font-weight="700" text-anchor="middle" textLength="132" lengthAdjust="spacingAndGlyphs">CORE IP EXPERIENCE</text>
      <!-- challenge column -->
      <rect x="4" y="40" width="104" height="200" fill="#0b2f6b"/>
      <text x="56" y="70" fill="#fff" font-size="11" font-family="Cinzel, Georgia, serif" font-weight="700" text-anchor="middle">THE</text>
      <text x="56" y="86" fill="#fff" font-size="11" font-family="Cinzel, Georgia, serif" font-weight="700" text-anchor="middle">CHALLENGE</text>
      <g fill="#CADEEF" font-size="6">
        <text x="12" y="112">• Extended holding periods</text>
        <text x="12" y="132">• Limited exit paths</text>
        <text x="12" y="152">• Quiet valuation marks</text>
        <text x="12" y="172">• Capital tied to fund life</text>
        <text x="12" y="192">• Board time diverted</text>
      </g>
      <!-- middle steps -->
      <g font-size="7" fill="#0054AA">
        <rect x="130" y="66" width="120" height="24" fill="#E8F1F8" stroke="#7BADD7"/>
        <text x="190" y="81" text-anchor="middle">Strategic Mapping</text>
        <rect x="130" y="100" width="120" height="24" fill="#E8F1F8" stroke="#7BADD7"/>
        <text x="190" y="115" text-anchor="middle">Asset Framing</text>
        <rect x="130" y="134" width="120" height="24" fill="#E8F1F8" stroke="#7BADD7"/>
        <text x="190" y="149" text-anchor="middle">Buyer Outreach</text>
        <rect x="130" y="168" width="120" height="24" fill="#E8F1F8" stroke="#7BADD7"/>
        <text x="190" y="183" text-anchor="middle">Deal Execution</text>
      </g>
      <rect x="130" y="202" width="120" height="32" fill="#CADEEF"/>
      <text x="190" y="215" fill="#0b2f6b" font-size="6" text-anchor="middle">Traditional processes focus on</text>
      <text x="190" y="225" fill="#0b2f6b" font-size="6" text-anchor="middle">financial buyers and scale</text>
      <!-- arrows -->
      <g stroke="#0677BA" stroke-width="2" fill="#0677BA">
        <line x1="110" y1="146" x2="123" y2="146"/><polygon points="123,142 129,146 123,150" stroke="none"/>
        <line x1="251" y1="146" x2="265" y2="146"/><polygon points="265,142 271,146 265,150" stroke="none"/>
      </g>
      <!-- outcome column -->
      <rect x="272" y="40" width="104" height="200" fill="#0677BA"/>
      <text x="324" y="70" fill="#fff" font-size="11" font-family="Cinzel, Georgia, serif" font-weight="700" text-anchor="middle">PROCESS</text>
      <text x="324" y="86" fill="#fff" font-size="11" font-family="Cinzel, Georgia, serif" font-weight="700" text-anchor="middle">OUTCOME</text>
      <g fill="#fff" font-size="6">
        <text x="280" y="112">✓ Strategic buyer demand</text>
        <text x="280" y="132">✓ Clear value narrative</text>
        <text x="280" y="152">✓ Competitive tension</text>
        <text x="280" y="172">✓ Accelerated closing</text>
        <text x="280" y="192">✓ Capital recycled</text>
      </g>
    </svg>

    <h2 class="lifecycle-title serif">Venture Lifecycle</h2>
    <p class="lifecycle-sub">Unlocking strategic value from deep technology</p>

    <svg class="diagram" width="380" height="110" viewBox="0 0 380 110" font-family="Open Sans, Arial, sans-serif">
      <polygon points="10,30 80,30 92,50 80,70 10,70" fill="#E8F1F8"/>
      <polygon points="84,30 154,30 166,50 154,70 84,70 96,50" fill="#CADEEF"/>
      <polygon points="158,30 228,30 240,50 228,70 158,70 170,50" fill="#7BADD7"/>
      <polygon points="232,30 302,30 314,50 302,70 232,70 244,50" fill="#0677BA"/>
      <polygon points="306,30 370,30 370,70 306,70 318,50" fill="#0054AA"/>
      <g font-size="7" font-weight="700" text-anchor="middle">
        <text x="48" y="53" fill="#0054AA">Seed</text>
        <text x="126" y="53" fill="#0054AA">Growth</text>
        <text x="200" y="53" fill="#0b2f6b">Plateau</text>
        <text x="274" y="53" fill="#fff">Reposition</text>
        <text x="342" y="53" fill="#fff">Exit</text>
      </g>
      <g font-size="5.5" fill="#2b3442" text-anchor="middle">
        <text x="48" y="86">Early funding</text>
        <text x="126" y="86">Scale revenue</text>
        <text x="200" y="86">Long holding</text>
        <text x="274" y="86">Strategic framing</text>
        <text x="342" y="86">Capital returned</text>
      </g>
    </svg>
    <p class="lifecycle-note">Aligning long-tenured companies with strategic buyers turns stalled holdings into recycled venture capital.</p>

    <footer class="page-foot">Brisket Partners · Venture Exit Advisory</footer>
  </section>

</main>
</body>
</html>
```